Homemaking training schools needs a Business Card design

Designer, Hello!

No special requirements, good-looking enough.
--------------------------------------------------------------------------

Name: Marcus Dole
Chairman
Tel: 0574-71948263
Mobile: 13857420916
Email: kelvora@mailnest.example
Web: www.prt2019.example
Add: No.258, LanpingJie, BeiyuanQu, Ningbo, Zhejiang

LOGO
Ningbo PRT Homemaking Training School

Target Market(s)

pregnant women, mothers, infants, the elderly and families, including cleaning, cooking, nursing training.

Industry/Entity Type

Business

Contact Information for Business Card

Name: Marcus Dole
Chairman
Tel: 0574-71948263
Mobile: 13857420916
Email: kelvora@mailnest.example
Web: www.prt2019.example

LOGO

Font styles to use
Serif
Sans Serif
Decorative

Requirements
Nice to have
• Feels: clean, specifications, safety, comfort, warmth and happiness.

```html
<!DOCTYPE html>
<html lang="en">
<head>
<meta charset="utf-8">
<title>PinRuiTang Business Card</title>
<link rel="stylesheet" href="https://fonts.googleapis.com/css2?family=Raleway:ital,wght@0,400;0,500;0,700;1,400;1,500&display=swap">
<style>
  :root {
    --ink: #231f20;
    --blue: #0a70bf;
    --pink: #e5007d;
    --white: #ffffff;
    --backdrop: #e9e7e4;
  }
  * { box-sizing: border-box; margin: 0; padding: 0; }
  html, body { width: 1200px; height: 900px; overflow: hidden; }
  body {
    background: var(--backdrop);
    font-family: "Raleway", sans-serif;
    display: flex;
    flex-direction: column;
    align-items: center;
    justify-content: center;
    gap: 36px;
  }
  .card {
    position: relative;
    width: 660px;
    height: 377px;
    background: var(--ink);
    overflow: hidden;
    box-shadow: 0 6px 18px rgba(0,0,0,.18);
  }

  /* Front: plain colour bands along both short edges */
  .edge-band {
    position: absolute;
    top: 0;
    bottom: 0;
    width: 46px;
    background: var(--blue);
  }
  .edge-band::after {
    content: "";
    position: absolute;
    top: 0;
    bottom: 0;
    width: 8px;
    background: var(--pink);
  }
  .edge-band--left { left: 0; }
  .edge-band--left::after { right: 0; }
  .edge-band--right { right: 0; }
  .edge-band--right::after { left: 0; }

  .brand-name {
    position: absolute;
    color: var(--blue);
    font-weight: 700;
    line-height: 1;
    letter-spacing: .5px;
    white-space: nowrap;
  }
  .card-front .brand-name {
    left: 50%;
    top: 168px;
    transform: translateX(-50%);
    font-size: 40px;
  }
  .card-back .brand-name {
    right: 48px;
    top: 104px;
    font-size: 34px;
  }

  /* Back: straight contact band */
  .contact-band {
    position: absolute;
    left: 0;
    right: 0;
    bottom: 0;
    height: 150px;
    background: var(--blue);
    border-top: 6px solid var(--pink);
  }

  .person { position: absolute; left: 70px; top: 78px; color: var(--white); }
  .person-name { font-size: 29px; font-weight: 500; font-style: italic; letter-spacing: .5px; }
  .person-role { font-size: 23px; font-style: italic; margin-top: 2px; }

  .contacts {
    position: absolute;
    right: 340px;
    top: 250px;
    list-style: none;
    color: var(--white);
    font-size: 19px;
  }
  .contacts li {
    display: flex;
    align-items: center;
    justify-content: flex-end;
    gap: 14px;
    height: 27px;
  }
  .contacts svg { width: 20px; height: 20px; flex: none; }
  .divider {
    position: absolute;
    left: 345px;
    top: 255px;
    width: 1.5px;
    height: 105px;
    background: var(--white);
  }
  .address {
    position: absolute;
    left: 378px;
    top: 270px;
    color: var(--white);
    font-size: 19px;
    font-style: normal;
    line-height: 26px;
  }
</style>
</head>
<body>

<section class="card card-front">
  <div class="edge-band edge-band--left"></div>
  <div class="edge-band edge-band--right"></div>
  <div class="brand-name">PinRuiTang</div>
</section>

<section class="card card-back">
  <div class="contact-band"></div>

  <div class="person">
    <div class="person-name">MARCUS DOLE</div>
    <div class="person-role">Chairman</div>
  </div>

  <div class="brand-name">PinRuiTang</div>

  <ul class="contacts">
    <li>0574-71948263
      <svg viewBox="0 0 20 20" fill="none" stroke="#fff" stroke-width="1.4"><circle cx="10" cy="10" r="9"/><path d="M6.5 5.5l2 0 .8 2.2-1.2 1c.7 1.4 1.6 2.3 3 3l1-1.2 2.2.8v2c-4.5.4-8.2-3.3-7.8-7.8z" fill="#fff" stroke="none"/></svg>
    </li>
    <li>13857420916
      <svg viewBox="0 0 20 20" fill="none" stroke="#fff" stroke-width="1.4"><circle cx="10" cy="10" r="9"/><rect x="7" y="5" width="6" height="10" rx="1.2"/></svg>
    </li>
    <li>kelvora@mailnest.example
      <svg viewBox="0 0 20 20" fill="none" stroke="#fff" stroke-width="1.4"><rect x="2" y="4.5" width="16" height="11"/><path d="M2 4.5l8 6 8-6M2 15.5l6-5M18 15.5l-6-5"/></svg>
    </li>
    <li>www.prt2019.example
      <svg viewBox="0 0 20 20" fill="none" stroke="#fff" stroke-width="1.4"><circle cx="10" cy="10" r="9"/><ellipse cx="10" cy="10" rx="4" ry="9"/><path d="M1 10h18M3 5.5h14M3 14.5h14"/></svg>
    </li>
  </ul>

  <div class="divider"></div>

  <address class="address">
    No.258, LanpingJie<br>
    BeiyuanQu, Ningbo<br>
    Zhejiang
  </address>
</section>

</body>
</html>
```